e-commerce store for sport clothing online store "baseball merchandise "web application...

I want to design a UX/UI for my web application website for the online store I will provide you with the following:
1. screen shots of the initial design for the pages>
2. the logo files.
3. The brand guideline file.

the provided files (screen shots) is guideline I want to see CREATIVITY with the UX/UI DESIGN.
PS. PLEASE FOLLOW THE BRANDGUIDE LINE CAREFULLY SPECIALLY THE TYPOGRAPHY & THE COLOR CODES.

PLEASE VISIT THIS WEBSITE brightlane.varomi-qz.com to see more for the screens.

```html
<!DOCTYPE html>
<html lang="en">
<head>
<meta charset="utf-8">
<title>Dugout Supply – Shop</title>
<link href="https://fonts.googleapis.com/css2?family=Open+Sans:wght@400;600;700&display=swap" rel="stylesheet">
<style>
:root{
  --navy:#0c2147;
  --red:#b00d2e;
  --heart:#e8334a;
  --heart-bg:#ffe6ea;
  --ink:#2b2b2b;
  --muted:#9a9a9a;
  --line:#e3e3e3;
  --field:#f4f4f5;
  --page:#e9e9ea;
  --white:#ffffff;
}
*{box-sizing:border-box;margin:0;padding:0}
html,body{width:1200px;height:2438px;overflow:hidden}
body{background:linear-gradient(180deg,#dcdcdd 0%,#ececed 20%,var(--page) 100%);font-family:"Open Sans",sans-serif;color:var(--ink)}
.stage{position:absolute;left:0;top:0;width:1268px;height:2576px;transform:scale(.94637);transform-origin:0 0}
.brand-hero{position:absolute;left:0;top:170px;width:1268px;display:flex;justify-content:center;align-items:center;gap:26px}
.brand-hero .dot{width:70px;height:70px;border-radius:50%;background:var(--navy)}
.brand-hero .name{font-size:72px;font-weight:700;color:var(--navy);letter-spacing:2px}

.screen{position:absolute;left:42px;width:1184px;background:var(--white);overflow:hidden;box-shadow:0 2px 10px rgba(0,0,0,.06)}
.screen.shop{top:506px;height:996px}
.screen.detail{top:1563px;height:950px}
.abs{position:absolute}

.topbar{position:absolute;left:0;top:0;width:100%;height:72px;border-bottom:1px solid var(--line)}
.topbar .mark{position:absolute;left:43px;top:26px;display:flex;align-items:center;gap:6px;font-size:13px;font-weight:700;color:var(--navy)}
.topbar .mark i{width:18px;height:18px;border-radius:50%;background:var(--navy);display:block}
.nav a{position:absolute;top:26px;font-size:15px;color:#333;text-decoration:none}
.nav a.active{font-weight:700;color:var(--navy)}
.nav .underline{position:absolute;left:405px;top:69px;width:37px;height:2px;background:var(--navy)}
.icons svg{position:absolute;top:24px}
.avatar{position:absolute;left:1116px;top:24px;width:25px;height:25px;border-radius:50%;background:linear-gradient(135deg,#7fbf6a,#4c8f3f);border:2px solid #cfe6c6}
.badge{position:absolute;left:1049px;top:37px;width:9px;height:9px;border-radius:50%;background:var(--heart)}

.sidebar{position:absolute;left:0;top:72px;width:288px;bottom:0;border-right:1px solid var(--line)}
.side-label{position:absolute;left:43px;font-size:15px;color:#333}
.divider{position:absolute;left:0;width:288px;height:1px;background:var(--line)}
.check{position:absolute;left:43px;display:flex;align-items:center;gap:12px;font-size:15px;color:#333}
.check .box{width:14px;height:14px;border:1px solid #bbb;border-radius:2px;display:flex;align-items:center;justify-content:center}
.check .box.on{background:var(--navy);border-color:var(--navy)}
.other{position:absolute;left:69px;font-size:15px;color:#333}
.field{position:absolute;height:39px;border-radius:3px;font-size:15px;display:flex;align-items:center;justify-content:center}
.field.min{background:#ececed;color:#aaa}
.field.max{border:1px solid #bbb;color:#333}
.btn{position:absolute;display:flex;align-items:center;justify-content:center;border-radius:3px;color:var(--white);font-size:15px;font-weight:600}
.btn.red{background:var(--red)}
.btn.navy{background:var(--navy)}
.promo{position:absolute;left:43px;width:202px;height:267px;border-radius:4px;background:radial-gradient(circle at 50% 65%,#4a4a4e 0%,#2a3550 45%,#16284a 100%);overflow:hidden}
.promo h3{position:absolute;left:18px;top:30px;font-size:19px;font-weight:600;color:var(--white)}
.promo p{position:absolute;left:18px;top:68px;width:170px;font-size:15px;line-height:28px;color:#eee}
.promo .code{position:absolute;left:18px;top:141px;width:152px;height:39px;background:var(--white);border-radius:2px;font-size:15px;color:#bbb;padding-left:18px;line-height:39px}
.promo .btn{left:18px;top:193px;width:152px;height:39px}

.search{position:absolute;left:327px;top:116px;width:657px;height:54px;background:var(--field);border-radius:4px}
.search .ph{position:absolute;left:55px;top:16px;font-size:15px;color:#999}
.search svg{position:absolute}

.card{position:absolute;width:235px;height:310px;border:1px solid var(--line);border-radius:4px;background:var(--white)}
.card .photo{position:absolute;left:35px;top:22px;width:165px;height:155px;border-radius:6px}
.card .title{position:absolute;left:20px;top:196px;font-size:15px;color:#222}
.card .price{position:absolute;left:20px;top:221px;font-size:15px;color:#222}
.card .btn{left:21px;top:258px;width:179px;height:39px}
.fav{position:absolute;width:26px;height:26px;border-radius:5px;display:flex;align-items:center;justify-content:center}
.fav.on{background:var(--heart-bg)}

.product-photo{position:absolute;left:327px;top:222px;width:319px;height:326px;border:1px solid var(--line);border-radius:4px}
.product-photo .photo{position:absolute;left:25px;top:20px;width:268px;height:290px;border-radius:8px;background:linear-gradient(90deg,#1d3a80 0 18%,#f7f7f7 18% 82%,#1d3a80 82%)}
.thumb{position:absolute;top:573px;width:99px;height:98px;background:#eef3f8;border-radius:3px}
.thumb .photo{position:absolute;left:25px;top:12px;width:50px;height:74px;border-radius:6px;background:linear-gradient(90deg,#1d3a80 0 22%,#fff 22% 78%,#1d3a80 78%)}
.p-title{position:absolute;left:694px;top:218px;font-size:22px;font-weight:600;color:#222}
.stars{position:absolute;left:694px;top:261px;display:flex;align-items:center;gap:1px}
.stars span{margin-left:8px;font-size:14px;color:#555}
.desc{position:absolute;left:694px;top:298px;width:460px;font-size:15px;line-height:28px;color:#444}
.desc em{font-style:normal;color:var(--red)}
.opt-label{position:absolute;left:694px;font-size:17px;color:#333}
.swatch{position:absolute;top:444px;width:36px;height:36px;border-radius:50%}
.swatch.sel{box-shadow:0 0 0 2px var(--white),0 0 0 3px #999}
.size{position:absolute;top:544px;width:52px;height:43px;border:1px solid #555;border-radius:2px;font-size:14px;display:flex;align-items:center;justify-content:center;color:#333}
.size.sel{background:var(--navy);border-color:var(--navy);color:var(--white);font-weight:600}
.p-price{position:absolute;left:694px;top:650px;font-size:21px;color:#222}
.scroll{position:absolute;left:1171px;top:72px;width:13px;height:924px;background:#f1f1f1}
.scroll i{position:absolute;left:3px;top:84px;width:7px;height:240px;background:#c4c4c4;border-radius:4px}
</style>
</head>
<body>
<div class="stage">

  <div class="brand-hero">
    <div class="dot"></div>
    <div class="name">DUGOUT SUPPLY</div>
  </div>

  <!-- Shop listing screen -->
  <section class="screen shop">
    <header class="topbar">
      <div class="mark"><i></i>Dugout Supply</div>
      <nav class="nav">
        <a style="left:326px">Home</a>
        <a class="active" style="left:405px">Shop</a>
        <a style="left:477px">Track Order</a>
        <a style="left:597px">Contact</a>
        <span class="underline"></span>
      </nav>
      <div class="icons">
        <svg style="left:1035px" width="20" height="22" viewBox="0 0 20 22" fill="none" stroke="#222" stroke-width="1.5"><path d="M3 7h14l-1 13H4z"/><path d="M7 7V5a3 3 0 0 1 6 0v2"/></svg>
        <span class="badge"></span>
        <svg style="left:1075px" width="24" height="22" viewBox="0 0 24 22" fill="none" stroke="#222" stroke-width="1.6"><path d="M12 20S3 14.5 2 9a5 5 0 0 1 10-2 5 5 0 0 1 10 2c-1 5.5-10 11-10 11z"/></svg>
        <span class="avatar" role="img" aria-label="User avatar"></span>
      </div>
    </header>

    <aside class="sidebar">
      <div class="side-label" style="top:23px">Filter</div>
      <div class="divider" style="top:64px"></div>
      <div class="side-label" style="top:86px">Categories</div>
      <label class="check" style="top:128px"><span class="box on"><svg width="10" height="8" viewBox="0 0 10 8"><path d="M1 4l3 3 5-6" stroke="#fff" stroke-width="1.6" fill="none"/></svg></span>Clothing</label>
      <label class="check" style="top:166px"><span class="box on"><svg width="10" height="8" viewBox="0 0 10 8"><path d="M1 4l3 3 5-6" stroke="#fff" stroke-width="1.6" fill="none"/></svg></span>Caps</label>
      <label class="check" style="top:204px"><span class="box"></span>Glove</label>
      <label class="check" style="top:242px"><span class="box"></span>Helmet</label>
      <div class="other" style="top:280px">Other &#8964;</div>
      <div class="divider" style="top:329px"></div>
      <div class="side-label" style="top:358px">Price Range</div>
      <div class="field min" style="left:43px;top:400px;width:94px">Min</div>
      <div class="field max" style="left:151px;top:400px;width:95px">$ 100</div>
      <div class="btn red" style="left:43px;top:451px;width:202px;height:39px">Set Price</div>
      <div class="divider" style="top:524px"></div>
      <div class="promo" style="top:567px" role="img" aria-label="Baseball in glove background">
        <h3>Get 25% Off</h3>
        <p>Enter cupon code and get discount!</p>
        <div class="code">Enter Code</div>
        <div class="btn red">Submit</div>
      </div>
    </aside>

    <div class="search">
      <svg style="left:24px;top:17px" width="20" height="20" viewBox="0 0 20 20" fill="none" stroke="#888" stroke-width="1.6"><circle cx="8" cy="8" r="6.5"/><path d="M13 13l5 5"/></svg>
      <span class="ph">Search</span>
      <svg style="left:616px;top:20px" width="14" height="14" viewBox="0 0 14 14" stroke="#666" stroke-width="1.5"><path d="M1 1l12 12M13 1L1 13"/></svg>
    </div>

    <div class="card" style="left:327px;top:222px">
      <div class="photo" role="img" aria-label="White raglan baseball shirt with black sleeves" style="background:linear-gradient(90deg,#1a1a1a 0 20%,#f8f8f8 20% 80%,#1a1a1a 80%)"></div>
      <div class="fav on" style="left:193px;top:16px"><svg width="14" height="13" viewBox="0 0 24 22"><path d="M12 20S3 14.5 2 9a5 5 0 0 1 10-2 5 5 0 0 1 10 2c-1 5.5-10 11-10 11z" fill="#e8334a"/></svg></div>
      <div class="title">Baseball T-shirt</div><div class="price">$ 50</div>
      <div class="btn navy">Add to cart</div>
    </div>
    <div class="card" style="left:617px;top:222px">
      <div class="photo" role="img" aria-label="White raglan baseball shirt with red sleeves" style="background:linear-gradient(90deg,#a3122a 0 20%,#f8f8f8 20% 80%,#a3122a 80%)"></div>
      <div class="fav" style="left:193px;top:16px"><svg width="14" height="13" viewBox="0 0 24 22"><path d="M12 20S3 14.5 2 9a5 5 0 0 1 10-2 5 5 0 0 1 10 2c-1 5.5-10 11-10 11z" fill="none" stroke="#aaa" stroke-width="2"/></svg></div>
      <div class="title">Baseball T-shirt</div><div class="price">$ 50</div>
      <div class="btn navy">Add to cart</div>
    </div>
    <div class="card" style="left:907px;top:222px">
      <div class="photo" role="img" aria-label="Red baseball cap" style="background:radial-gradient(ellipse at 55% 55%,#e0222c 0 38%,#fff 40%)"></div>
      <div class="fav" style="left:193px;top:16px"><svg width="14" height="13" viewBox="0 0 24 22"><path d="M12 20S3 14.5 2 9a5 5 0 0 1 10-2 5 5 0 0 1 10 2c-1 5.5-10 11-10 11z" fill="none" stroke="#aaa" stroke-width="2"/></svg></div>
      <div class="title">Baseball Cap</div><div class="price">$ 50</div>
      <div class="btn navy">Add to cart</div>
    </div>

    <div class="card" style="left:327px;top:570px">
      <div class="photo" role="img" aria-label="Royal blue baseball cap" style="background:radial-gradient(ellipse at 55% 55%,#1f45b8 0 38%,#fff 40%)"></div>
      <div class="fav" style="left:193px;top:16px"><svg width="14" height="13" viewBox="0 0 24 22"><path d="M12 20S3 14.5 2 9a5 5 0 0 1 10-2 5 5 0 0 1 10 2c-1 5.5-10 11-10 11z" fill="none" stroke="#aaa" stroke-width="2"/></svg></div>
      <div class="title">Baseball T-shirt</div><div class="price">$ 50</div>
      <div class="btn navy">Add to cart</div>
    </div>
    <div class="card" style="left:617px;top:570px">
      <div class="photo" role="img" aria-label="White raglan baseball shirt with green sleeves" style="background:linear-gradient(90deg,#3a9a2f 0 20%,#f8f8f8 20% 80%,#3a9a2f 80%)"></div>
      <div class="fav on" style="left:193px;top:16px"><svg width="14" height="13" viewBox="0 0 24 22"><path d="M12 20S3 14.5 2 9a5 5 0 0 1 10-2 5 5 0 0 1 10 2c-1 5.5-10 11-10 11z" fill="#e8334a"/></svg></div>
      <div class="title">Baseball T-shirt</div><div class="price">$ 50</div>
      <div class="btn navy">Add to cart</div>
    </div>
    <div class="card" style="left:907px;top:570px">
      <div class="photo" role="img" aria-label="Navy and grey trucker cap" style="background:radial-gradient(ellipse at 55% 55%,#c9c9cc 0 22%,#233a78 24% 38%,#fff 40%)"></div>
      <div class="fav" style="left:193px;top:16px"><svg width="14" height="13" viewBox="0 0 24 22"><path d="M12 20S3 14.5 2 9a5 5 0 0 1 10-2 5 5 0 0 1 10 2c-1 5.5-10 11-10 11z" fill="none" stroke="#aaa" stroke-width="2"/></svg></div>
      <div class="title">Baseball T-shirt</div><div class="price">$ 50</div>
      <div class="btn navy">Add to cart</div>
    </div>

    <div class="card" style="left:327px;top:915px">
      <div class="photo" role="img" aria-label="White raglan baseball shirt with black sleeves" style="background:linear-gradient(90deg,#1a1a1a 0 20%,#f8f8f8 20% 80%,#1a1a1a 80%)"></div>
      <div class="fav on" style="left:193px;top:16px"><svg width="14" height="13" viewBox="0 0 24 22"><path d="M12 20S3 14.5 2 9a5 5 0 0 1 10-2 5 5 0 0 1 10 2c-1 5.5-10 11-10 11z" fill="#e8334a"/></svg></div>
    </div>
    <div class="card" style="left:617px;top:915px">
      <div class="photo" role="img" aria-label="White raglan baseball shirt with red sleeves" style="background:linear-gradient(90deg,#a3122a 0 20%,#f8f8f8 20% 80%,#a3122a 80%)"></div>
      <div class="fav" style="left:193px;top:16px"><svg width="14" height="13" viewBox="0 0 24 22"><path d="M12 20S3 14.5 2 9a5 5 0 0 1 10-2 5 5 0 0 1 10 2c-1 5.5-10 11-10 11z" fill="none" stroke="#aaa" stroke-width="2"/></svg></div>
    </div>
    <div class="card" style="left:907px;top:915px">
      <div class="photo" role="img" aria-label="Red baseball cap" style="background:radial-gradient(ellipse at 55% 55%,#e0222c 0 38%,#fff 40%)"></div>
      <div class="fav" style="left:193px;top:16px"><svg width="14" height="13" viewBox="0 0 24 22"><path d="M12 20S3 14.5 2 9a5 5 0 0 1 10-2 5 5 0 0 1 10 2c-1 5.5-10 11-10 11z" fill="none" stroke="#aaa" stroke-width="2"/></svg></div>
    </div>

    <div class="scroll"><i></i></div>
  </section>

  <!-- Product detail screen -->
  <section class="screen detail">
    <header class="topbar">
      <div class="mark"><i></i>Dugout Supply</div>
      <nav class="nav">
        <a style="left:326px">Home</a>
        <a class="active" style="left:405px">Shop</a>
        <a style="left:477px">Track Order</a>
        <a style="left:597px">Contact</a>
        <span class="underline"></span>
      </nav>
      <div class="icons">
        <svg style="left:1035px" width="20" height="22" viewBox="0 0 20 22" fill="none" stroke="#222" stroke-width="1.5"><path d="M3 7h14l-1 13H4z"/><path d="M7 7V5a3 3 0 0 1 6 0v2"/></svg>
        <span class="badge"></span>
        <svg style="left:1075px" width="24" height="22" viewBox="0 0 24 22" fill="none" stroke="#222" stroke-width="1.6"><path d="M12 20S3 14.5 2 9a5 5 0 0 1 10-2 5 5 0 0 1 10 2c-1 5.5-10 11-10 11z"/></svg>
        <span class="avatar" role="img" aria-label="User avatar"></span>
      </div>
    </header>

    <aside class="sidebar">
      <div class="side-label" style="top:23px">Filter</div>
      <div class="divider" style="top:64px"></div>
      <div class="side-label" style="top:86px">Categories</div>
      <label class="check" style="top:128px"><span class="box on"><svg width="10" height="8" viewBox="0 0 10 8"><path d="M1 4l3 3 5-6" stroke="#fff" stroke-width="1.6" fill="none"/></svg></span>Clothing</label>
      <label class="check" style="top:166px"><span class="box on"><svg width="10" height="8" viewBox="0 0 10 8"><path d="M1 4l3 3 5-6" stroke="#fff" stroke-width="1.6" fill="none"/></svg></span>Caps</label>
      <label class="check" style="top:204px"><span class="box"></span>Glove</label>
      <label class="check" style="top:242px"><span class="box"></span>Helmet</label>
      <div class="other" style="top:280px">Other &#8964;</div>
      <div class="divider" style="top:329px"></div>
      <div class="side-label" style="top:358px">Price Range</div>
      <div class="field min" style="left:43px;top:400px;width:94px">Min</div>
      <div class="field max" style="left:151px;top:400px;width:95px">$ 100</div>
      <div class="btn red" style="left:43px;top:451px;width:202px;height:39px">Set Price</div>
      <div class="divider" style="top:524px"></div>
      <div class="promo" style="top:567px" role="img" aria-label="Baseball in glove background">
        <h3>Get 25% Off</h3>
        <p>Enter cupon code and get discount!</p>
        <div class="code">Enter Code</div>
        <div class="btn red">Submit</div>
      </div>
    </aside>

    <div class="search">
      <svg style="left:24px;top:17px" width="20" height="20" viewBox="0 0 20 20" fill="none" stroke="#888" stroke-width="1.6"><circle cx="8" cy="8" r="6.5"/><path d="M13 13l5 5"/></svg>
      <span class="ph">Search</span>
      <svg style="left:616px;top:20px" width="14" height="14" viewBox="0 0 14 14" stroke="#666" stroke-width="1.5"><path d="M1 1l12 12M13 1L1 13"/></svg>
    </div>

    <div class="product-photo">
      <div class="photo" role="img" aria-label="White raglan shirt with navy sleeves"></div>
      <div class="fav on" style="left:275px;top:16px"><svg width="14" height="13" viewBox="0 0 24 22"><path d="M12 20S3 14.5 2 9a5 5 0 0 1 10-2 5 5 0 0 1 10 2c-1 5.5-10 11-10 11z" fill="#e8334a"/></svg></div>
    </div>
    <div class="thumb" style="left:327px"><div class="photo" role="img" aria-label="Shirt side view"></div></div>
    <div class="thumb" style="left:437px"><div class="photo" role="img" aria-label="Shirt back view"></div></div>
    <div class="thumb" style="left:547px"><div class="photo" role="img" aria-label="Shirt angled view"></div></div>

    <h1 class="p-title">Basketball T-shirt</h1>
    <div class="stars">
      <svg width="16" height="15" viewBox="0 0 24 23"><path d="M12 1l3.3 7 7.7.8-5.8 5.2 1.7 7.6L12 17.7 5.1 21.6l1.7-7.6L1 8.8 8.7 8z" fill="#f2b01e"/></svg>
      <svg width="16" height="15" viewBox="0 0 24 23"><path d="M12 1l3.3 7 7.7.8-5.8 5.2 1.7 7.6L12 17.7 5.1 21.6l1.7-7.6L1 8.8 8.7 8z" fill="#f2b01e"/></svg>
      <svg width="16" height="15" viewBox="0 0 24 23"><path d="M12 1l3.3 7 7.7.8-5.8 5.2 1.7 7.6L12 17.7 5.1 21.6l1.7-7.6L1 8.8 8.7 8z" fill="#f2b01e"/></svg>
      <svg width="16" height="15" viewBox="0 0 24 23"><path d="M12 1l3.3 7 7.7.8-5.8 5.2 1.7 7.6L12 17.7 5.1 21.6l1.7-7.6L1 8.8 8.7 8z" fill="#f2b01e"/></svg>
      <svg width="16" height="15" viewBox="0 0 24 23"><path d="M12 1l3.3 7 7.7.8-5.8 5.2 1.7 7.6L12 17.7 5.1 21.6l1.7-7.6L1 8.8 8.7 8z" fill="none" stroke="#999" stroke-width="1.5"/></svg>
      <span>( 32 Reviews )</span>
    </div>
    <p class="desc">Lorem ipsum dolor sit amet, consectetur adipiscing elit, sed do eiusmod tempor incididunt ut labore et dolore magna aliquad. Quis ipsum suspendisse ultrices gravida. <em>More</em></p>

    <div class="opt-label" style="top:402px">Color</div>
    <span class="swatch sel" style="left:694px;background:var(--navy)"></span>
    <span class="swatch" style="left:745px;background:#f3262b"></span>
    <span class="swatch" style="left:796px;background:#279a25"></span>
    <span class="swatch" style="left:847px;background:#e8bf22"></span>

    <div class="opt-label" style="top:504px">Size</div>
    <span class="size" style="left:694px">XS</span>
    <span class="size" style="left:760px">S</span>
    <span class="size sel" style="left:826px">M</span>
    <span class="size" style="left:892px">L</span>
    <span class="size" style="left:958px">XL</span>
    <span class="size" style="left:1024px">2XL</span>
    <span class="size" style="left:1090px">3XL</span>

    <div class="p-price">$ 50.00</div>
    <div class="btn navy" style="left:961px;top:645px;width:178px;height:38px">Buy Now</div>
  </section>

</div>
</body>
</html>
```